Employee Benefits Flyer for Recruiting

We are a Steel Product Supplier and Manufacturer in Toledo Ohio.

We would like to create an "attention getting", one-page handout to give prospective employees (both production and administrative) that illustrates all the benefits we offer as a company. An editable document would be preferable as we add more or change existing benefits in the future. Current benefits include:

Individual and Family Medical Insurance
Dental Insurance
Vision Insurance
Short Term Disability Insurance
Critical Illness and Accident Insurance
No Cost Life Insurance Policy
Education Cost Reimbursement
401K with Company Match
Profit Sharing
Attendance and Performance Bonuses
No Cost Legal Assistance
No Cost Counseling Services
No Cost Tobacco Cessation Coaching
No Cost College Planning Assistance
No Cost Work-Life Services
No Cost Employee Discounts
No Cost Legal Consultation
No Cost Financial Consultation
No Cost ID Theft Assistance
No Cost Tax Consultation Assistance
Up to 17 Days of Paid Time Off

Target Market(s)

Potential Employees

Industry/Entity Type

Industrial Manufacturing

Requirements
Must have
• Nicely laid out illustrations / engaging content

```html
<!DOCTYPE html>
<html lang="en">
<head>
<meta charset="utf-8">
<title>We Are Hiring – Keystone Metal Works</title>
<link rel="stylesheet" href="https://fonts.googleapis.com/css2?family=Yellowtail&family=Oswald:wght@700&family=Montserrat:ital,wght@0,700;1,700&display=swap">
<style>
  :root {
    --backdrop: #1b1b1b;
    --blue-deep: #0a3aa8;
    --blue-bright: #0a6cff;
    --ink-blue: #1c3f8e;
    --label-grey: #8c8c8c;
    --white: #ffffff;
  }
  * { margin: 0; padding: 0; box-sizing: border-box; }
  html, body { width: 1200px; height: 1200px; overflow: hidden; background: var(--backdrop); }
  .flyer {
    position: absolute; left: 176px; top: 0;
    width: 848px; height: 1200px;
    background: var(--white); overflow: hidden;
  }
  .flyer-shapes { position: absolute; inset: 0; }
  .brand {
    position: absolute; right: 30px; top: 30px; width: 200px;
    text-align: center; color: var(--white);
    font-family: "Montserrat", sans-serif; font-weight: 700;
  }
  .brand-dot {
    width: 78px; height: 78px; border-radius: 50%;
    background: var(--white); margin: 0 auto 14px;
  }
  .brand-name { font-size: 15px; letter-spacing: 0.5px; line-height: 1.2; }
  .headline-script {
    position: absolute; left: 0; width: 848px; top: 165px;
    text-align: center; padding-right: 20px;
    font-family: "Yellowtail", cursive; font-size: 132px; line-height: 1;
    color: var(--white);
  }
  .headline-main {
    position: absolute; left: 0; width: 848px; top: 262px;
    text-align: center;
    font-family: "Oswald", sans-serif; font-weight: 700;
    font-size: 176px; line-height: 1; letter-spacing: 2px;
    color: var(--white);
  }
  .offerings-label {
    position: absolute;
    font-family: "Oswald", sans-serif; font-weight: 700;
    font-size: 72px; line-height: 1; letter-spacing: 1px;
    color: var(--label-grey);
    transform: rotate(-90deg); transform-origin: left top;
    white-space: nowrap;
  }
  .offerings-label.left { left: 38px; top: 1066px; }
  .offerings-label.right { left: 436px; top: 1068px; }
  .benefit-list {
    position: absolute; list-style: none;
    font-family: "Montserrat", sans-serif; font-style: italic; font-weight: 700;
    font-size: 17.5px; line-height: 28.2px;
    color: var(--ink-blue); letter-spacing: 0.2px;
  }
  .benefit-list.left { left: 115px; top: 700px; width: 320px; }
  .benefit-list.right { left: 516px; top: 672px; width: 320px; }
  .site-url {
    position: absolute; left: 0; width: 848px; top: 1158px;
    text-align: center;
    font-family: "Montserrat", sans-serif; font-weight: 700;
    font-size: 19px; letter-spacing: 3px; color: var(--white);
  }
</style>
</head>
<body>
<main class="flyer">
  <svg class="flyer-shapes" viewBox="0 0 848 1200" width="848" height="1200">
    <defs>
      <linearGradient id="topBlue" x1="0" y1="0" x2="1" y2="0">
        <stop offset="0" stop-color="#0a3aa8"/>
        <stop offset="0.55" stop-color="#0a6cff"/>
        <stop offset="1" stop-color="#0a44c0"/>
      </linearGradient>
      <linearGradient id="photoTone" x1="0" y1="0" x2="1" y2="1">
        <stop offset="0" stop-color="#2a3f63"/>
        <stop offset="0.5" stop-color="#51688c"/>
        <stop offset="1" stop-color="#2b5fa8"/>
      </linearGradient>
      <linearGradient id="silverArc" x1="0" y1="0" x2="1" y2="0">
        <stop offset="0" stop-color="#9a9a9a"/>
        <stop offset="0.6" stop-color="#e6e6e6"/>
        <stop offset="1" stop-color="#ffffff"/>
      </linearGradient>
    </defs>
    <rect class="top-band" width="848" height="700" fill="url(#topBlue)"/>
    <path class="building-photo" role="img" aria-label="Aerial photograph of the company's blue-trimmed steel plant building"
          d="M0,270 C170,110 470,55 848,235 L848,470 C700,585 460,625 240,565 C130,535 55,505 0,475 Z"
          fill="url(#photoTone)"/>
    <path class="silver-arc" d="M0,525 C220,660 560,680 848,410 L848,440 C560,700 220,690 0,560 Z" fill="url(#silverArc)"/>
    <path class="body-panel" d="M0,560 C220,690 560,700 848,440 L848,1200 L0,1200 Z" fill="#ffffff"/>
    <path class="bottom-band" d="M0,1075 C250,1150 600,1150 848,1088 L848,1200 L0,1200 Z" fill="url(#topBlue)"/>
  </svg>

  <div class="brand">
    <div class="brand-dot"></div>
    <div class="brand-name">KEYSTONE METAL WORKS</div>
  </div>

  <div class="headline-script">We are</div>
  <h1 class="headline-main">HIRING</h1>

  <div class="offerings-label left">OFFERINGS</div>
  <ul class="benefit-list left">
    <li>Individual and Family Medical Insurance</li>
    <li>Dental Insurance</li>
    <li>Vision Insurance</li>
    <li>Short Term Disability Insurance</li>
    <li>Critical Illness and Accident Insurance</li>
    <li>No Cost Life Insurance Policy</li>
    <li>Education Cost Reimbursement</li>
    <li>401K with Company Match</li>
    <li>Profit Sharing</li>
    <li>Attendance and Performance Bonuses</li>
  </ul>

  <div class="offerings-label right">OFFERINGS</div>
  <ul class="benefit-list right">
    <li>No Cost Legal Assistance</li>
    <li>No Cost Counseling Services</li>
    <li>No Cost Tobacco Cessation Coaching</li>
    <li>No Cost College Planning Assistance</li>
    <li>No Cost Work-Life Services</li>
    <li>No Cost Employee Discounts</li>
    <li>No Cost Legal Consultation</li>
    <li>No Cost Financial Consultation</li>
    <li>No Cost ID Theft Assistance</li>
    <li>No Cost Tax Consultation Assistance</li>
    <li>Up to 17 Days of Paid Time Off</li>
  </ul>

  <div class="site-url">WWW.KEYSTONE-METALWORKS.COM</div>
</main>
</body>
</html>
```